Private Investment Firm Needs PowerPoint Presentation Template

Design PowerPoint template, take Pinebrook-submitted rough presentation draft, and drop it into new template. See attached Project Brief file for more detail.
Updates

Some decent designs have been submitted but they seem to lack the understanding of our target markets. I am hopeful that more time and feedback will result in better results.

Target Market(s)

Private company owners and intermediaries.

Font styles to use
Serif

Colors
3176b5

Requirements
Must have
• See attached Project Brief.
Nice to have
Should not have
• No B2C fluff--this is a B2B project.

```html
<!DOCTYPE html>
<html lang="en">
<head>
<meta charset="utf-8">
<title>Pinebrook Capital – Firm Overview</title>
<link rel="stylesheet" href="https://fonts.googleapis.com/css2?family=Arimo:wght@400;700&family=Tinos:wght@400;700&family=Carlito:wght@400;700&display=swap">
<style>
:root{
  --blue:#1f72c4;
  --brand:#3176b5;
  --navy:#1d5fa8;
  --grey-text:#6b6b6b;
  --ink:#222;
  --panel:#dce6f0;
  --sheet:#c9c9c9;
  --row-a:#e6e6e6;
  --row-b:#f3f3f3;
}
*{margin:0;padding:0;box-sizing:border-box}
html,body{width:845px;height:1200px;overflow:hidden;background:var(--sheet)}
.deck{position:relative;width:845px;height:1200px}
.slide{position:absolute;width:417px;height:235px;background:#fff;overflow:hidden;font-family:"Tinos",serif;color:var(--ink)}
.c1{left:3px}.c2{left:425px}
.r1{top:3px}.r2{top:242px}.r3{top:482px}.r4{top:722px}.r5{top:962px}

.side-panel{position:absolute;right:0;top:0;width:77px;height:100%;background:var(--panel)}
.accent{position:absolute;left:10px;top:0;width:10px;height:30px;background:var(--blue)}
.title{position:absolute;left:23px;top:30px;font:700 13.5px/1.1 "Arimo",sans-serif;color:var(--blue);letter-spacing:.1px}
.title.two-line{top:26px;font-size:13px}

.footer-mark{position:absolute;left:6px;top:208px;display:flex;align-items:center;gap:3px}
.footer-mark .dot{width:11px;height:11px;border-radius:50%;background:var(--brand)}
.footer-mark .name{font:400 8px/1 "Tinos",serif;color:#444;letter-spacing:.4px}
.footer-mark .name small{display:block;font-size:3.4px;letter-spacing:2px;color:#666;margin-top:1px}
.footer-line{position:absolute;left:76px;top:220px;width:304px;height:7px;background:var(--blue)}
.footer-square{position:absolute;left:398px;top:213px;width:19px;height:16px;background:var(--blue)}

.label{position:absolute;font:700 13px/16.5px "Arimo",sans-serif;text-align:right}
.label .g{color:var(--grey-text)}
.label .b{color:var(--blue)}

ul.bullets{position:absolute;list-style:none;font-size:8.6px;line-height:13.7px;color:#333}
ul.bullets li{position:relative;padding-left:10px}
ul.bullets li::before{content:"•";position:absolute;left:0}
ul.bullets ul{list-style:none;padding-left:6px}

/* cover */
.cover-photo{position:absolute;inset:0}
.cover-mark{position:absolute;left:77px;top:76px;display:flex;align-items:center;gap:12px}
.cover-mark .dot{width:60px;height:60px;border-radius:50%;background:var(--brand)}
.cover-mark .word{font:400 30px/1 "Tinos",serif;color:#3a3a3a;letter-spacing:2px}
.cover-mark .sub{font:400 15px/1 "Tinos",serif;color:#3a3a3a;letter-spacing:14px;margin-top:4px;border-bottom:1px solid #999;padding-bottom:3px}
.cover-mark .tag{font:400 8.6px/1 "Tinos",serif;color:var(--brand);letter-spacing:1.2px;margin-top:5px;font-variant:small-caps}
.cover-title{position:absolute;right:6px;top:199px;font:700 13.5px/15px "Arimo",sans-serif;text-align:right;color:#111}

/* portfolio slides */
.case{position:absolute;font-size:5.1px;line-height:6.2px;color:#222}
.case .use{color:var(--navy)}
.brand{position:absolute;font:700 11px/1 "Tinos",serif;color:var(--navy);text-align:center}

/* table */
.impact{position:absolute;left:123px;top:78px;width:214px;border-collapse:collapse;font-family:"Carlito",sans-serif;font-size:6.8px}
.impact th{background:var(--navy);color:#fff;font-weight:700;padding:3px 4px;text-align:center;border-right:1px solid #fff}
.impact th:first-child{width:100px}
.impact td{padding:2.2px 4px;text-align:center;border-right:1px solid #fff;border-bottom:1px solid #fff}
.impact td:first-child{text-align:left}
.impact tr:nth-child(odd) td{background:var(--row-a)}
.impact tr:nth-child(even) td{background:var(--row-b)}
.note{position:absolute;left:124px;top:144px;width:140px;font-size:6.4px;line-height:8px;color:var(--navy)}
.caveat{position:absolute;right:80px;top:190px;width:200px;text-align:right;font:400 6.2px/8px "Arimo",sans-serif;color:var(--blue)}
</style>
</head>
<body>
<div class="deck">

  <section class="slide c1 r1 cover">
    <svg class="cover-photo" width="417" height="235" role="img" aria-label="Photo strips of glass office towers against a blue sky">
      <defs>
        <linearGradient id="sky" x1="0" y1="0" x2="1" y2="1">
          <stop offset="0" stop-color="#5ea6e3"/><stop offset="1" stop-color="#1e5f9e"/>
        </linearGradient>
        <linearGradient id="glass" x1="0" y1="0" x2="1" y2="1">
          <stop offset="0" stop-color="#2d4a6b"/><stop offset="1" stop-color="#7fb0d8"/>
        </linearGradient>
      </defs>
      <polygon points="52,72 105,0 155,0 102,72" fill="url(#sky)"/>
      <polygon points="112,72 165,0 215,0 162,72" fill="url(#sky)"/>
      <polygon points="172,72 225,0 417,0 417,30 385,72" fill="url(#sky)"/>
      <polygon points="0,235 0,165 300,165 248,235" fill="url(#glass)"/>
      <polygon points="258,235 310,165 365,165 312,235" fill="url(#glass)"/>
    </svg>
    <div class="cover-mark">
      <div class="dot"></div>
      <div>
        <div class="word">PINEBROOK</div>
        <div class="sub">CAPITAL</div>
        <div class="tag">Non-Control Growth Capital</div>
      </div>
    </div>
    <div class="cover-title">FIRM<br>OVERVIEW</div>
  </section>

  <section class="slide c2 r1">
    <div class="side-panel"></div>
    <div class="accent"></div>
    <h2 class="title">PINEBROOK CAPITAL INTRODUCTION</h2>
    <ul class="bullets" style="left:20px;top:50px;width:310px;line-height:11.4px;font-size:9px">
      <li>Pinebrook invests Non-Control Capital direct with management
        <ul><li>Owners retain control of their business after we invest</li>
        <li>Without a traditional Change-of-Control private equity sponsor</li></ul></li>
      <li style="margin-top:3px">One of the longest-standing junior capital funds targeting the lower middle market</li>
      <li style="margin-top:3px">Since 1994, Pinebrook has completed 74 (and counting) Non-Control Capital investments and managed over $600 million</li>
      <li style="margin-top:3px">Our interests are aligned with management or we don’t invest</li>
      <li style="margin-top:3px">“Consultants with Capital”
        <ul><li>We partner with companies that seek capital <b><u>and</u></b> our assistance to improve and/or grow the business</li></ul></li>
    </ul>
    <div class="footer-mark"><span class="dot"></span><span class="name">PINEBROOK<small>CAPITAL</small></span></div>
    <div class="footer-line"></div><div class="footer-square"></div>
  </section>

  <section class="slide c1 r2">
    <div class="side-panel"></div>
    <div class="accent"></div>
    <h2 class="title">OVERVIEW</h2>
    <div class="label" style="left:20px;top:56px;width:112px">
      <span class="b">WE HAVE<br>OVER</span><br><span class="g">140 YEARS</span><br><span class="b">OF<br>COMBINED<br>PRINCIPAL<br>INVESTING<br>EXPERIENCE<br>.</span>
    </div>
    <ul class="bullets" style="left:138px;top:56px;width:200px">
      <li>Offices in Boston and San Francisco with 12 investment professionals <b><u>fully dedicated </u></b> to Non-Control Capital investing</li>
      <li>Invest combinations of equity and subordinated debt securities</li>
      <li>Currently investing $260MM fourth fund
        <ul><li>9 Fund IV investments made to date (as of November 1, 2018)</li>
        <li>Over $120MM of “dry powder” available for new investments</li></ul></li>
    </ul>
    <div class="footer-mark"><span class="dot"></span><span class="name">PINEBROOK<small>CAPITAL</small></span></div>
    <div class="footer-line"></div><div class="footer-square"></div>
  </section>

  <section class="slide c2 r2">
    <div class="side-panel"></div>
    <div class="accent"></div>
    <h2 class="title">WHAT WE DO / AND WHY</h2>
    <div class="label" style="left:20px;top:95px;width:118px">
      <span class="g">NON-CONTROL</span><br><span class="b">CAPITAL<br>TRANSACTIONS<br>ONLY</span>
    </div>
    <ul class="bullets" style="left:142px;top:80px;width:195px">
      <li>Companies looking for a partner to help them grow, not sellers looking to exit</li>
      <li>Management’s personal wealth directly tied to the performance of the investment</li>
      <li>Situational investors with a generalist approach</li>
      <li>Our heritage reflects decades of Non-Control Capital investing—it’s all we do</li>
    </ul>
    <div class="footer-mark"><span class="dot"></span><span class="name">PINEBROOK<small>CAPITAL</small></span></div>
    <div class="footer-line"></div><div class="footer-square"></div>
  </section>

  <section class="slide c1 r3">
    <div class="side-panel"></div>
    <div class="accent"></div>
    <h2 class="title two-line">PINEBROOK REPRESENTATIVE NON-CONTROL<br>CAPITAL INVESTMENTS</h2>
    <div class="brand" style="left:6px;top:73px;width:70px;font-size:9px">Skyward Flight Group</div>
    <p class="case" style="left:77px;top:58px;width:262px">♦ Operates dedicated commercial airline pilot training facilities throughout the U.S. and Mexico. Centers are complete with classrooms; integrated procedures trainers; flight training devices; and Level D, full-motion flight simulators.<br><span class="use">♦ Pinebrook’s capital was used to fund the Company’s near to intermediate-term growth. Pinebrook also assisted the Company in the recruitment of additional management personnel and the opening of a new Dallas office.</span></p>
    <p class="case" style="left:12px;top:103px;width:258px;text-align:right">♦ Manufacturer of vibration isolation, seismic control, and shock protection products. The Company’s products are designed to limit the transmission of vibration, impact, seismic, and wind forces to protect larger systems that are at risk of damage from these events.<br><span class="use">♦ Pinebrook’s capital was used to acquire two attractive tuck-in companies (a testing lab and an on-line component distributor) that improved KVR’s competitive position. Three years later, the Company set an all-time sales record.</span></p>
    <div class="brand" style="left:273px;top:108px;width:62px;height:28px;background:#111;color:#fff;font-size:7px;line-height:28px">THE KVR GROUP</div>
    <div class="brand" style="left:6px;top:171px;width:66px;font-size:9px;color:#c4202f">Ridgeline Alarm</div>
    <p class="case" style="left:77px;top:143px;width:262px">♦ Provider of fire and security alarm design, installation, service, and monitoring services for commercial and residential end-markets.<br><span class="use">♦ Pinebrook’s capital allowed for enough cash breathing room for the CEO to think strategically about the business, focus on the growth of the Company, and build family wealth. Five years later, after the Company and Pinebrook were successful in substantially growing the business, Ridgeline Alarm bought out Pinebrook’s ownership position entirely with senior debt—as a result, the CEO (father), COO (son), and key management team were back to owning 100% of the Company. The son had a significantly larger stake in the business than five years earlier and the father had the flexibility to work through his family estate plans.</span></p>
    <div class="footer-mark"><span class="dot"></span><span class="name">PINEBROOK<small>CAPITAL</small></span></div>
    <div class="footer-line"></div><div class="footer-square"></div>
  </section>

  <section class="slide c2 r3">
    <div class="side-panel"></div>
    <div class="accent"></div>
    <h2 class="title two-line">PINEBROOK REPRESENTATIVE NON-CONTROL<br>CAPITAL INVESTMENTS</h2>
    <div class="brand" style="left:10px;top:70px;width:100px;font-size:12px">HOLLIS<br><span style="font-size:5px;font-weight:700">MANAGEMENT CONSULTING</span></div>
    <p class="case" style="left:118px;top:62px;width:222px">♦ Provider of audit compliance software and consulting services for hospitals and physician practices.<br><span class="use">♦ Pinebrook’s capital was used to assist the active CEO in acquiring the business from its inactive founder. Pinebrook also assisted in the significant investment into the Company’s core revenue integrity software platform, developing it into the premier risk-based product in its sector.</span></p>
    <p class="case" style="left:5px;top:116px;width:250px;text-align:right">♦ Provider of third-party vehicle maintenance services for private, public, and for-hire fleet-based businesses nationwide.<br><span class="use">♦ Pinebrook’s capital was used to support Fairway’s accelerating growth which exceeded their current lender’s capacity. Pinebrook provided both subordinated debt and preferred stock, altered the debt and equity mix of the business, and the Company was able to grow significantly over the next three years.</span></p>
    <div class="brand" style="left:258px;top:122px;width:82px;font-size:12px;color:#333">Fairway<br><span style="font-size:4.5px;letter-spacing:1px">FLEET SOLUTIONS</span></div>
    <div class="brand" style="left:10px;top:170px;width:74px;font-size:11px;color:#111">Orion<br>Corporation</div>
    <p class="case" style="left:92px;top:170px;width:248px">♦ Provides comprehensive and custom packaging for the liquid home cleaning products sector, and has the ability to safely process volatile liquids, such as bleach and hydrogen peroxide.<br><span class="use">♦ Pinebrook’s capital was used to assist a New York-based family office in acquiring the Company as part of their business outsourcing growth strategy thesis.</span></p>
    <div class="footer-mark"><span class="dot"></span><span class="name">PINEBROOK<small>CAPITAL</small></span></div>
    <div class="footer-line"></div><div class="footer-square"></div>
  </section>

  <section class="slide c1 r4">
    <div class="side-panel"></div>
    <div class="accent"></div>
    <h2 class="title">INVESTMENT CRITERIA</h2>
    <div class="label" style="left:10px;top:74px;width:122px">
      <span class="g">PINEBROOK<br>INVESTS IN</span><br><span class="b">ESTABLISHED,<br>LOWER MIDDLE<br>MARKET<br>COMPANIES</span>
    </div>
    <ul class="bullets" style="left:138px;top:74px;width:205px;white-space:nowrap">
      <li>Revenues of $10MM to $150MM</li>
      <li>EBITDA of at least $2MM</li>
      <li>Pinebrook investment size of $5MM to $25MM</li>
      <li>Experienced, committed, and incented management</li>
      <li>Limited leverage (aka debt) “ahead” of Pinebrook</li>
      <li>Niche market leader with differentiated services or<br>products</li>
      <li>Focused on value-added execution, not proof of concept</li>
    </ul>
    <div class="footer-mark"><span class="dot"></span><span class="name">PINEBROOK<small>CAPITAL</small></span></div>
    <div class="footer-line"></div><div class="footer-square"></div>
  </section>

  <section class="slide c2 r4">
    <div class="side-panel"></div>
    <div class="accent"></div>
    <h2 class="title">CONSULTANTS WITH CAPITAL</h2>
    <div class="label" style="left:2px;top:74px;width:94px">
      <span class="g">WE HELP</span><br><span class="b">PORTFOLIO<br>COMPANIES<br>CREATE<br>GREATER<br>VALUE.</span>
    </div>
    <ul class="bullets" style="left:102px;top:56px;width:240px;white-space:nowrap">
      <li>Facilitate strategy development</li>
      <li>Improve financial reporting and information systems</li>
      <li>Assist with key hires, such as CFOs and COOs, if needed</li>
      <li>Source, evaluate, finance, close, and integrate acquisitions</li>
      <li>Invest additional capital</li>
      <li>Annual Executive Summit focused on professional<br>development and networking</li>
      <li>Most importantly, act as a sounding board to help solve<br>problems, identify new opportunities, and create value</li>
      <li>We personally invest in every transaction</li>
    </ul>
    <p class="caveat">These options are made available to our portfolio companies, if needed, and not forced upon them</p>
    <div class="footer-mark"><span class="dot"></span><span class="name">PINEBROOK<small>CAPITAL</small></span></div>
    <div class="footer-line"></div><div class="footer-square"></div>
  </section>

  <section class="slide c1 r5">
    <div class="side-panel"></div>
    <div class="accent"></div>
    <h2 class="title">PINEBROOK IMPACT - BY THE NUMBERS</h2>
    <div class="label" style="left:6px;top:60px;width:112px">
      <span class="g">DURING<br>PINEBROOK’S<br>AVERAGE<br>INVESTMENT<br>TERM,</span><br><span class="b">OUR IMPACT<br>HAS BEEN<br>NOTEWORTHY</span>
    </div>
    <table class="impact">
      <thead><tr><th>Impact Category</th><th>Actual<br>Impact</th><th>Min/Max*<br>Removed</th></tr></thead>
      <tbody>
        <tr><td>Average Revenue Growth</td><td>113%</td><td>91%</td></tr>
        <tr><td>Average EBITDA Growth</td><td>75%</td><td>78%</td></tr>
        <tr><td>Average Employee Growth</td><td>213%</td><td>49%</td></tr>
      </tbody>
    </table>
    <p class="note">*Note: Actual Impact figures based on 55 exited investments from 1994 to 2017. Min/Max removed from each of 3 fully invested funds.</p>
    <div class="footer-mark"><span class="dot"></span><span class="name">PINEBROOK<small>CAPITAL</small></span></div>
    <div class="footer-line"></div><div class="footer-square"></div>
  </section>

  <section class="slide c2 r5">
    <div class="side-panel"></div>
    <div class="accent"></div>
    <h2 class="title">IN SUMMARY</h2>
    <ul class="bullets" style="left:20px;top:56px;width:312px;font-size:8.4px;line-height:10px">
      <li>There is an alternative to giving up control of your company through an infusion of Non-Control Capital</li>
      <li style="margin-top:4px">All investors are not created equal</li>
      <li style="margin-top:4px">Non-Control Capital investing is a specialty:
        <ul style="font-size:7.6px;line-height:9px"><li>Choose only an investor with decades of Non-Control heritage, experience, and focus (<span style="color:var(--navy)">see Questionnaire in the Epilogue section of this presentation</span>)</li></ul></li>
      <li style="margin-top:4px">It means more than just capital:
        <ul style="font-size:7.6px;line-height:9px"><li>Team up with an accomplished investor who can bring demonstrated growth abilities, not simply write a check</li></ul></li>
      <li style="margin-top:4px">Chemistry between company management and the investor is critical:
        <ul style="font-size:7.6px;line-height:9px"><li>If Pinebrook’s interests are not aligned with management, we don’t invest</li></ul></li>
    </ul>
    <div class="footer-mark"><span class="dot"></span><span class="name">PINEBROOK<small>CAPITAL</small></span></div>
    <div class="footer-line"></div><div class="footer-square"></div>
  </section>

</div>
</body>
</html>
```